New Company Logo & Responsive Website Design for Codeworks Heron

Codeworks Heron provides a white labeled, digital lending platform technology solutions to the mortgage industry via a SaaS model. Our target market is Mortgage Companies and Banks who are looking for innovative technology to assist both borrowers and loan originators with the lending process, while automating as much of he process as possible.

Codeworks Heron is our company name, and our modular software offerings Include the following Products:

1) Applicant Heron: A customizable, web based, point-of-sale application for borrowers to complete a loan application, and guide them through the mortgage process.

POS Definition
"A point of sale (POS) is the client-facing software solution that allows borrowers to create a customer portal, apply for a loan online, and seamlessly submit needed documentation."

2) Ledger Heron: A Mortgage Loan Origination System

LOS Definition
"A Mortgage Loan Origination System (LOS) is a platform that takes a completed loan application and facilitates the mortgage transaction from origination to post closing. LOS systems may include document management, pricing and eligibility engines, and compliance tools to decrease risk and increase loan manufacturing quality.

3) Dwelling Heron: A brandable, home search website

The LOS and POS definitions provided above are just for your understanding of what these products are, not to be included word-for-word as website content.

We are looking for designs that are elegant, convey technical competency, simple to navigate, and set us apart from the competition.

We are not set on any particular colors at this point, so feel free to choose the best colors for your particular designs.

Please include company logo, both desktop and mobile designs with a template design for the website sub pages.

Some Examples of Mortgage Technology Websites offering similar products. These are to show the typical content, not designs that we particularly like or dislike.

https://brantiq.example/
https://www.clearvantro.example/
https://www.abodefundbuddy.example/
https://www.debtquokka.example/
https://www.ternixapps.example/products/trail

Please send comments with additional questions.

Thank You For your participation.

Mortgage Companies

```html
<!DOCTYPE html>
<html lang="en">
<head>
<meta charset="utf-8">
<title>Codeworks Heron — Mortgage FinTech Startup</title>
<link rel="stylesheet" href="https://fonts.googleapis.com/css2?family=Poppins:wght@400;500;600;700&family=Roboto:ital,wght@0,400;0,500;1,400&display=swap">
<style>
:root{
  --blue:#2a73d0;
  --blue-deep:#1f63bd;
  --orange:#f88a1c;
  --ink:#333a44;
  --muted:#666c75;
  --white:#ffffff;
  --footer:#050505;
  --line:#e4e8ee;
}
*{box-sizing:border-box;margin:0;padding:0}
html,body{width:1200px;height:3798px;overflow:hidden}
body{position:relative;background:var(--white);font-family:"Roboto",Arial,sans-serif;color:var(--ink)}
.abs{position:absolute}
.hero-bg{position:absolute;left:0;top:0;width:1200px;height:800px}
.brand{font-family:"Poppins",sans-serif;font-weight:500;color:var(--white)}
.site-logo{left:112px;top:30px;font-size:34px}
.main-nav{left:510px;top:46px;display:flex;gap:31px;font-family:"Poppins",sans-serif;font-size:14.5px;color:var(--white);text-transform:uppercase}
.hero-title{left:112px;top:228px;font-family:"Poppins",sans-serif;font-weight:700;font-size:37px;color:var(--white);white-space:nowrap}
.hero-sub{left:112px;top:288px;font-family:"Poppins",sans-serif;font-weight:600;font-size:32px;color:var(--white);white-space:nowrap}
.hero-text{left:112px;top:346px;width:440px;font-family:"Poppins",sans-serif;font-size:15.5px;line-height:34px;color:#eaf1fb;white-space:nowrap}
.btn-start{left:112px;top:472px;width:187px;height:59px;border-radius:30px;background:var(--orange);color:var(--white);font-family:"Poppins",sans-serif;font-weight:600;font-size:18px;display:flex;align-items:center;justify-content:center}
.hero-visual{left:572px;top:162px;width:571px;height:610px;border-radius:14px;background:linear-gradient(160deg,#d9dadd 0%,#8a8f96 40%,#3b3f45 70%,#c7c9cc 100%)}
.section-title{left:0;width:1200px;text-align:center;font-family:"Poppins",sans-serif;font-weight:600;color:var(--ink)}
.title-bar{width:58px;height:3px;background:var(--blue);left:571px}
.service-card{top:962px;width:310px;height:379px;background:var(--white);border-radius:14px;box-shadow:0 2px 10px rgba(0,0,0,.12);border-bottom:4px solid var(--blue);text-align:center}
.service-card.is-orange{border-bottom-color:var(--orange)}
.service-icon{position:absolute;left:107px;top:26px;width:96px;height:96px;border-radius:50%}
.service-name{position:absolute;left:0;width:100%;top:168px;font-family:"Poppins",sans-serif;font-weight:500;font-size:26px;color:#3d434b}
.service-bar{position:absolute;left:134px;top:212px;width:42px;height:3px;background:var(--blue)}
.is-orange .service-bar{background:var(--orange)}
.service-text{position:absolute;left:26px;right:26px;top:232px;font-size:14px;line-height:26px;color:var(--muted)}
.shot{width:376px;height:305px;border-radius:4px;background:var(--white);box-shadow:0 2px 10px rgba(0,0,0,.15);overflow:hidden}
.shot-bar{height:30px;background:#f4f5f7;display:flex;gap:6px;align-items:center;padding-left:14px}
.shot-bar i{width:8px;height:8px;border-radius:50%;background:#c7cbd1;display:block}
.shot-body{position:absolute;left:10px;right:10px;top:40px;bottom:10px;border-radius:3px}
.step-num{width:48px;height:48px;border-radius:50%;background:var(--white);box-shadow:0 1px 6px rgba(0,0,0,.12);font-family:"Poppins",sans-serif;font-weight:600;font-size:22px;color:var(--blue);display:flex;align-items:center;justify-content:center}
.step-icon{width:88px;height:88px;border-radius:50%;background:var(--blue);border:5px solid #cfe0f5;display:flex;align-items:center;justify-content:center}
.step-icon.is-orange{background:var(--orange);border-color:#fde0c2}
.step-head{font-family:"Poppins",sans-serif;font-weight:500;font-size:20px;color:#3a3f47;white-space:nowrap}
.step-lead{font-family:"Poppins",sans-serif;font-size:21px;line-height:34px;color:var(--blue);white-space:nowrap}
.step-lead.is-orange{color:var(--orange)}
.step-text{font-size:13.5px;line-height:26px;color:var(--muted);text-align:justify;width:426px}
.testimonials{left:0;top:2889px;width:1200px;height:484px;background:var(--blue)}
.avatar{left:542px;top:3029px;width:121px;height:121px;border-radius:50%;background:radial-gradient(circle at 50% 40%,#d8a98a,#6b4636);border:3px solid #5b9be2}
.quote{left:240px;top:3166px;width:720px;text-align:center;font-style:italic;font-size:15px;line-height:28px;color:var(--white)}
.quote-mark{display:inline-block;height:16px;line-height:40px;vertical-align:top;font-family:"Poppins",sans-serif;font-weight:700;font-size:40px;color:var(--white);font-style:normal;margin:0 6px}
.quote-mark.is-close{vertical-align:-14px}
.quote-name{left:0;width:1200px;top:3294px;text-align:center;font-family:"Poppins",sans-serif;font-size:17px;color:var(--white)}
.arrow-box{width:42px;height:40px;border:1.5px solid var(--white);display:flex;align-items:center;justify-content:center}
.site-footer{left:0;top:3373px;width:1200px;height:425px;background:var(--footer)}
.footer-logo{left:0;width:1200px;top:3405px;text-align:center;font-size:40px}
.footer-nav{left:0;width:1200px;top:3496px;display:flex;justify-content:center;gap:33px;font-family:"Poppins",sans-serif;font-size:15px;color:var(--white);text-transform:uppercase}
.contact-item{top:3567px;width:260px;text-align:center;color:var(--white);font-size:14px;line-height:25px}
.contact-icon{width:66px;height:66px;border-radius:50%;margin:0 auto 12px;display:flex;align-items:center;justify-content:center;border:2px solid var(--blue)}
.contact-icon.is-filled{background:var(--blue)}
.footer-rule{left:112px;top:3717px;width:976px;height:1px;background:#2b2b2b}
.social{top:3742px;width:34px;height:34px;border-radius:50%;border:1.5px solid var(--white)}
.copyright{right:112px;top:3748px;font-size:14px;color:var(--white)}
</style>
</head>
<body>

<svg class="hero-bg" viewBox="0 0 1200 800" aria-hidden="true">
  <path d="M0 0H1200V498C1010 556 800 606 610 690C500 738 420 782 300 768C190 754 90 700 0 663Z" fill="var(--blue)"/>
</svg>

<header>
  <div class="abs brand site-logo">Codeworks Heron</div>
  <nav class="abs main-nav"><span>Home</span><span>About Us</span><span>Services</span><span>Product</span><span>Features</span><span>Contact Us</span></nav>
</header>

<section class="hero">
  <h1 class="abs hero-title">CODEWORKS HERON</h1>
  <h2 class="abs hero-sub">Mortgage FinTech Startup</h2>
  <p class="abs hero-text">Sed ut perspiciatis unde omnis iste natus error sit vol<br>uptatem accusantium doloremque laudantium,&nbsp; aper<br>iam, eaque ipsa quae explicabo.</p>
  <div class="abs btn-start">GET STARTED</div>
  <div class="abs hero-visual" role="img" aria-label="Desktop monitor showing a desk photo with a tablet displaying SaaS cloud icons"></div>
</section>

<section class="services">
  <h2 class="abs section-title" style="top:848px;font-size:45px">Our Services</h2>
  <div class="abs title-bar" style="top:913px"></div>

  <div class="abs service-card" style="left:112px">
    <div class="service-icon" role="img" aria-label="Line icon of a hand holding a money bag" style="background:linear-gradient(#e3eefb,#cfe0f6)"></div>
    <div class="service-name">Applicant Heron</div><div class="service-bar"></div>
    <p class="service-text">A customizable, web based, point-of-sale application for borrowers to complete a loan application, and guide them through the mortgage process.</p>
  </div>
  <div class="abs service-card is-orange" style="left:445px">
    <div class="service-icon" role="img" aria-label="Line icon of a house with a dollar coin" style="background:linear-gradient(#fef0e0,#fbdcba)"></div>
    <div class="service-name">Ledger Heron</div><div class="service-bar"></div>
    <p class="service-text">A Mortgage Loan Origination System</p>
  </div>
  <div class="abs service-card" style="left:778px">
    <div class="service-icon" role="img" aria-label="Line icon of a property document with a dollar coin" style="background:linear-gradient(#e3eefb,#cfe0f6)"></div>
    <div class="service-name">Dwelling Heron</div><div class="service-bar"></div>
    <p class="service-text">A brandable, home search website</p>
  </div>
</section>

<section class="timeline">
  <h2 class="abs section-title" style="top:1430px;font-size:38px">Mortgage FinTech Startup</h2>
  <div class="abs title-bar" style="top:1488px"></div>

  <svg class="abs" style="left:0;top:1571px" width="1200" height="1318" viewBox="0 0 1200 1318" aria-hidden="true">
    <path d="M538 0V360C538 400 662 380 662 440V820C662 880 538 860 538 920V1318" fill="none" stroke="#cfd5dd" stroke-width="1.5" stroke-dasharray="3 4"/>
  </svg>

  <div class="abs shot" style="left:112px;top:1571px"><div class="shot-bar"><i></i><i></i><i></i></div><div class="shot-body" role="img" aria-label="Light UI kit screen with charts, sliders and calendar" style="background:linear-gradient(135deg,#eef3f9,#dfe8f3)"></div></div>
  <div class="abs step-num" style="left:514px;top:1636px">01</div>
  <div class="abs step-icon" style="left:612px;top:1565px">
    <svg width="38" height="34" viewBox="0 0 38 34" aria-hidden="true"><rect x="1" y="8" width="36" height="24" rx="3" fill="#fff"/><rect x="13" y="2" width="12" height="8" rx="2" fill="none" stroke="#fff" stroke-width="3"/><rect x="1" y="17" width="36" height="3" fill="var(--blue)"/><rect x="16" y="15" width="6" height="7" fill="var(--blue)"/></svg>
  </div>
  <h3 class="abs step-head" style="left:624px;top:1664px">Sed ut perspiciatis unde omnis iste</h3>
  <p class="abs step-lead" style="left:624px;top:1700px">Nemo enim ipsam voluptatem quia volu<br>ptas sit aspernatur</p>
  <p class="abs step-text" style="left:624px;top:1782px">Sed ut perspiciatis unde omnis iste natus error sit voluptatem acc usantium doloremque laudantium, totam rem aperiam, eaque ipsa quae ab illo inventore veritatis et quasi architecto beatae vitae dicta sunt explicabo.</p>

  <div class="abs step-icon is-orange" style="left:158px;top:2061px">
    <svg width="40" height="34" viewBox="0 0 40 34" aria-hidden="true"><path d="M4 12H12L28 3V31L12 22H4Z" fill="#fff"/><path d="M11 22L14 32H20L17 22" fill="#fff"/><path d="M32 11Q37 17 32 23" fill="none" stroke="#fff" stroke-width="3"/></svg>
  </div>
  <div class="abs step-num" style="left:638px;top:2047px">02</div>
  <h3 class="abs step-head" style="left:170px;top:2160px">Sed ut perspiciatis unde omnis iste</h3>
  <p class="abs step-lead is-orange" style="left:170px;top:2196px">Nemo enim ipsam voluptatem quia volu<br>ptas sit aspernatur</p>
  <p class="abs step-text" style="left:170px;top:2278px">Sed ut perspiciatis unde omnis iste natus error sit voluptatem acc usantium doloremque laudantium, totam rem aperiam, eaque ipsa quae ab illo inventore veritatis et quasi architecto beatae vitae dicta sunt explicabo.</p>
  <div class="abs shot" style="left:712px;top:2084px"><div class="shot-bar"><i></i><i></i><i></i></div><div class="shot-body" role="img" aria-label="Data overview dashboard with tables and small charts" style="background:linear-gradient(135deg,#f4f6f9,#e6ebf2)"></div></div>

  <div class="abs shot" style="left:112px;top:2503px"><div class="shot-bar"><i></i><i></i><i></i></div><div class="shot-body" role="img" aria-label="Analytics dashboard with bar, line and donut charts" style="background:linear-gradient(135deg,#f2f6fb,#e2ebf6)"></div></div>
  <div class="abs step-num" style="left:511px;top:2545px">03</div>
  <div class="abs step-icon" style="left:612px;top:2500px">
    <svg width="36" height="36" viewBox="0 0 36 36" aria-hidden="true"><path d="M20 5H6A3 3 0 0 0 3 8V30A3 3 0 0 0 6 33H28A3 3 0 0 0 31 30V16" fill="none" stroke="#fff" stroke-width="3"/><path d="M29 3L33 7L18 22L13 23L14 18Z" fill="#fff"/></svg>
  </div>
  <h3 class="abs step-head" style="left:624px;top:2597px">Sed ut perspiciatis unde omnis iste</h3>
  <p class="abs step-lead" style="left:624px;top:2632px">Nemo enim ipsam voluptatem quia volu<br>ptas sit aspernatur</p>
  <p class="abs step-text" style="left:624px;top:2715px">Sed ut perspiciatis unde omnis iste natus error sit voluptatem acc usantium doloremque laudantium, totam rem aperiam, eaque ipsa quae ab illo inventore veritatis et quasi architecto beatae vitae dicta sunt explicabo.</p>
</section>

<section class="abs testimonials"></section>
<h2 class="abs section-title" style="top:2936px;font-size:38px;color:var(--white)">Testimonials</h2>
<div class="abs title-bar" style="top:2996px;background:var(--white)"></div>
<div class="abs avatar" role="img" aria-label="Portrait photo of the client"></div>
<div class="abs arrow-box" style="left:127px;top:3162px"><svg width="10" height="14" viewBox="0 0 10 14" aria-hidden="true"><path d="M7 2L2 7L7 12" fill="none" stroke="#fff" stroke-width="1.6"/></svg></div>
<div class="abs arrow-box" style="left:1030px;top:3162px"><svg width="10" height="14" viewBox="0 0 10 14" aria-hidden="true"><path d="M3 2L8 7L3 12" fill="none" stroke="#fff" stroke-width="1.6"/></svg></div>
<p class="abs quote"><span class="quote-mark">“</span>Sed ut perspiciatis unde omnis iste natus error sit voluptatem accusantium doloremque laudantium,<br>totam rem aperiam, eaque ipsa quae ab illo inventore veritatis et quasi architecto beatae vitae dicta<br>sunt explicabo. Nemo enim ipsam voluptatem quia voluptas sit aspernatur aut odit aut fugit, sed quia<br>consequuntur magni dolores eos qui ratione voluptatem sequi nesciunt.<span class="quote-mark is-close">”</span></p>
<div class="abs quote-name">- MARA ELWIN</div>

<footer>
  <div class="abs site-footer"></div>
  <div class="abs brand footer-logo">Codeworks Heron</div>
  <nav class="abs footer-nav"><span>Home</span><span>About Us</span><span>Services</span><span>Product</span><span>Features</span><span>Contact Us</span></nav>

  <div class="abs contact-item" style="left:98px">
    <div class="contact-icon is-filled"><svg width="18" height="24" viewBox="0 0 18 24" aria-hidden="true"><path d="M9 1A8 8 0 0 0 1 9C1 15 9 23 9 23S17 15 17 9A8 8 0 0 0 9 1Z" fill="#fff"/><circle cx="9" cy="9" r="3" fill="var(--blue)"/></svg></div>
    PO Box Lorem Ipsum Dummy<br>Lorem 2163
  </div>
  <div class="abs contact-item" style="left:325px">
    <div class="contact-icon"><svg width="20" height="20" viewBox="0 0 20 20" aria-hidden="true"><path d="M4 1L8 5L6 8Q8 12 12 14L15 12L19 16L16 19Q8 19 1 4Z" fill="#fff"/></svg></div>
    +1 555 010 2040
  </div>
  <div class="abs contact-item" style="left:564px">
    <div class="contact-icon"><svg width="22" height="16" viewBox="0 0 22 16" aria-hidden="true"><rect x="1" y="1" width="20" height="14" rx="1" fill="#fff"/><path d="M1 2L11 9L21 2" fill="none" stroke="var(--footer)" stroke-width="1.6"/></svg></div>
    info@codeworksheron.example
  </div>
  <div class="abs contact-item" style="left:840px">
    <div class="contact-icon"><svg width="20" height="20" viewBox="0 0 20 20" aria-hidden="true"><circle cx="10" cy="10" r="9" fill="#fff"/><path d="M10 1Q5 10 10 19M10 1Q15 10 10 19M1 10H19" fill="none" stroke="var(--footer)" stroke-width="1.3"/></svg></div>
    www.codeworksheron.example
  </div>

  <div class="abs footer-rule"></div>
  <div class="abs social" style="left:119px" role="img" aria-label="Social profile link"></div>
  <div class="abs social" style="left:161px" role="img" aria-label="Social profile link"></div>
  <div class="abs social" style="left:204px" role="img" aria-label="Social profile link"></div>
  <div class="abs copyright">© Copyright 2022 Codeworks Heron.All Rights Reserved</div>
</footer>

</body>
</html>
```